Website development company website

ABOUT COMPANY
Hi everyone! We're a Melbourne, Australia website development company in a need of a website design that will make online store merchants want to engage our services.
We specialise exclusively in Torvista e-commerce platform (https://torvista-platform.example/). What distinguishes our business from competition is that rather than designing and building brand new websites, we offer development, support and maintenance services to established websites. Maintenance and Support are the keywords representing our business.
Our potential clients are people with broken, slow and underperforming Torvista installations who need assistance getting their websites up and making sales. Our website must pass the message that we can help, and provide quick means of making contact.
DESIGN
Overall, we're looking for a slick, clean, airy, conservative design. No need to do anything crazy, try to stick to what's "standard" in website design these days and make it easy on all of us. The website is unlikely to be updated too often so it needs to look attractive and fresh first time over and after a year, too.
Attached is our new logo, which you'll be able to take the basic idea from, the colors and fonts. Though, don't use the fonts from the logo in the website, stick to the standard widely supported fonts. Additional use of Google fonts is fine.
Don't overdo it with colors, stick to conservative basic color set and only use the colors from the log for accents like headings etc. Please, don't be tempted to use the blue and orange as background of whole blocks, other than perhaps footer. Thanks.
For the images used, I'd like to stay away from a design studio/digital agency feel and lean more towards professional support and maintenance services. I'm thinking images of content merchants doing their job. Something along the lines of "We'll be taking care of the website so that you only need to care about the business".
Some ideas I like:
http://www.plumframe-pics.example/detail/photo/portrait-of-confident-male-design-professional-royalty-free-image/572048163
http://www.plumframe-pics.example/detail/photo/designer-taking-picture-of-hat-high-res-stock-photography/839207514
http://www.plumframe-pics.example/detail/photo/woman-packaging-pottery-royalty-free-image/216684093
Images of colorful shopping bags and shopping carts are over the top and not serious enough. Instead of images matching Online Shopping, I'd try going more for Stability, Reliability, Performance.
Our existing website is http://www.bravuln.example. Please, don't take design ideas from it, but it will give you a picture of the structure of our new website and content that's going to be used initially.
If you could include a basic icon set to use throughout the website, that would be great. If the icons could match our logo (attached), it would be a big plus.
ALL PAGES
Every page must contain clearly visible phone number (1300 648 907) and a Contact Us Now button, which opens an AJAX driven popup form with Name, Email, Phone and Message to be sent through.
To start with, main menu items will be Torvista, Portfolio, Contact.
At the bottom of each page, please, include a newsletter subscription form with text Subscribe to Torvista Support and Security Updates.
For the footer, I'd like to see a logo strip with the following logos in grayscale (no need to link anywhere): Torvista, QRX, DataVane, NCB. You'll find the logos on Google Images.
Standard footer columns follow. Here, I'd like to see logos in color: Torvista Certified Developer, Torvista Ceritified Solution Provider. Again, the logos are on Google Images.
No social media logos/links necessary anywhere on the website.
...and then the copyright line.
FRONT PAGE
Large slider with images that would appeal to our target audience. Keywords here would be Torvista System Audit, Torvista Performance Optimisation, Torvista Website Emergency Recovery, Torvista Development Infrastructure Hosting. We'll have a static page created for each of these to link to.
In a corner of the slider, or on the edge, can I have an overlay with logos in color (same as footer): Torvista Certified Developer, Torvista Ceritified Solution Provider.
Underneath, a number of blocks, each with an image and teaser that we'll use to link to various pages throughout the website.
PORTFOLIO PAGE
I'm thinking a single long page with a block per client, which will contain project name, description from us and a testimonial from client. Also, each block will contain a single large screenshot. No gallery or slideshow is necessary here, just one image per project.
I'll leave the layout up to you, but try to put yourself in the shoes of a potential client reviewing our past work by simply scrolling down this one page.
CONTACT US PAGE
Separate page with the same form as above, phone number (1300 648 907), email address (support@kavreo.example), address (Suite 42, Level 3|8 Wattlebrook Lane|Fernvale Heights VIC 3999), and a grayscale Google Map.
CODING UP
Coding up into static HTML/CSS/JS is equally important as the design itself. We're a website development company, we'll be integrating the theme. We will spot any issues and we will point them out.
Coded up design must be fully responsive. Enough said.
To be able to create any content in future, we'd like one extra page coded up with samples of all themed elements, lists, forms, buttons, 2, 3, 4-column layout, alerts, icons, etc. This page does not need to be designed, only coded up.
The design will be integrated into Drupal using Twig. If possible at all, try to keep it in mind when designing and coding up, and make the integration into a Drupal theme easier for us.
GOOD LUCK!
That's it. Let me know if anything needs clarifying. So far I've had a great experience with ArtFlockly. I don't doubt some great designs will emerge. Clever ideas are highly appreciated, but also make it clear you've read and followed the points in this brief. Cheers, Tom

```html
<!DOCTYPE html>
<html lang="en">
<head>
<meta charset="utf-8">
<title>Kavreo E-Commerce – Torvista Support &amp; Maintenance</title>
<link rel="stylesheet" href="https://fonts.googleapis.com/css2?family=Ubuntu:wght@300;400;500&family=Open+Sans:ital,wght@0,400;0,600;0,700;1,400&display=swap">
<style>
:root{
  --orange:#e8781f;
  --orange-dark:#d4641a;
  --navy:#0c3a6e;
  --navy-dark:#0a2f5a;
  --ink:#333b45;
  --muted:#5a5f66;
  --light:#f4f4f4;
  --line:#dcdcdc;
  --white:#ffffff;
}
*{box-sizing:border-box;margin:0;padding:0}
html,body{width:1200px;height:2601px;overflow:hidden}
body{font-family:"Open Sans",Arial,sans-serif;color:var(--ink);background:var(--white);position:relative}
.section{position:absolute;left:0;width:1200px}
.heading{font-family:"Ubuntu",Arial,sans-serif;font-weight:400;color:var(--navy);font-size:25px;display:flex;align-items:center;gap:10px}
.heading-mark{width:12px;height:15px;background:var(--navy);display:inline-block}
.copy{font-size:11.5px;line-height:21px;color:var(--muted)}
.btn{display:inline-flex;align-items:center;justify-content:center;background:var(--orange);color:var(--white);font-size:11px;font-weight:700;text-transform:uppercase;height:40px;padding:0 16px;border-radius:2px;text-decoration:none}
.placeholder{position:absolute}

/* header */
.site-header{top:0;height:76px;border-top:3px solid var(--orange);background:var(--white);box-shadow:0 1px 3px rgba(0,0,0,.08);z-index:2}
.brand{position:absolute;left:162px;top:16px;display:flex;align-items:center;gap:8px;font-family:"Ubuntu",Arial,sans-serif;font-weight:500;font-size:26px;color:var(--orange)}
.brand-square{width:22px;height:26px;background:var(--navy)}
.main-nav{position:absolute;left:404px;top:30px;display:flex;gap:0}
.main-nav a{font-size:11px;color:var(--ink);text-decoration:none;text-transform:uppercase;margin-right:40px}
.main-nav a.active{color:var(--navy);font-weight:700}
.header-phone{position:absolute;left:803px;top:17px;display:flex;align-items:center;gap:14px}
.header-phone .label{font-size:12px;color:var(--navy);display:block}
.header-phone .number{font-family:"Ubuntu",Arial,sans-serif;font-size:18px;color:var(--orange);display:block;margin-top:2px}

/* hero */
.hero{top:76px;height:514px;background:linear-gradient(100deg,#3a2a1e 0%,#5a3f2a 40%,#8a6545 70%,#b08a6a 100%);overflow:hidden}
.hero-media{left:0;top:0;width:1200px;height:514px}
.hero-title{position:absolute;left:160px;top:190px;color:var(--white);font-family:"Ubuntu",Arial,sans-serif;font-weight:300}
.hero-title .l1{font-size:38px;display:block}
.hero-title .l2{font-size:52px;display:block;margin-top:2px}
.hero-dots{position:absolute;left:1128px;top:218px;display:flex;flex-direction:column;gap:7px}
.hero-dots span{width:12px;height:12px;border-radius:50%;background:var(--white)}
.hero-dots span.on{background:var(--orange)}
.hero-partners{position:absolute;left:792px;top:432px;display:flex;gap:26px;align-items:center}
.hero-partners span{font-family:"Ubuntu",Arial,sans-serif;font-size:20px;color:rgba(255,255,255,.85)}

/* services */
.services{top:590px;height:314px;background:var(--light)}
.service{position:absolute;top:37px;width:210px;text-align:center}
.service-icon{width:86px;height:86px;border-radius:50%;background:var(--navy);margin:0 auto;display:flex;align-items:center;justify-content:center}
.service-icon.orange{background:var(--orange)}
.service-title{margin-top:20px;font-size:13px;line-height:21px;color:var(--ink)}
.service-text{margin-top:10px;font-size:11px;line-height:19px;color:var(--muted)}
.service-link{display:block;margin-top:18px;font-size:10px;font-weight:700;color:var(--orange);text-decoration:none}

/* why us */
.why{top:904px;height:329px;background:var(--white)}
.why-body{position:absolute;left:160px;top:40px;width:470px}
.why-body .copy{margin-top:18px}
.why-body .copy + .copy{margin-top:12px}
.why-body .btn{margin-top:20px}
.why-media{left:700px;top:20px;width:410px;height:309px;background:linear-gradient(135deg,#f5f5f5,#e6e6e6);border-radius:4px}

/* what we do */
.what{top:1233px;height:308px;background:linear-gradient(90deg,#d9661c 0%,#e8781f 50%,#df6d1d 100%);text-align:center;color:var(--white)}
.what .heading{color:var(--white);justify-content:center;margin-top:52px}
.what .heading-mark{background:var(--white)}
.what-text{width:730px;margin:22px auto 0;font-size:11px;line-height:21px}
.btn-ghost{display:inline-flex;align-items:center;justify-content:center;margin-top:20px;width:110px;height:40px;border:1px solid var(--white);color:var(--white);font-size:11px;font-weight:700;text-decoration:none}

/* why platform */
.platform{top:1541px;height:349px;background:var(--white)}
.platform-media{left:160px;top:20px;width:340px;height:300px;background:linear-gradient(135deg,#f2f2f2,#dedede);border-radius:4px}
.platform-body{position:absolute;left:575px;top:46px;width:470px}
.platform-body .copy{margin-top:18px}
.platform-body .copy + .copy{margin-top:12px}
.platform-body .btn{margin-top:20px;width:277px}

/* testimonials */
.testimonials{top:1890px;height:268px;background:var(--light)}
.testimonials .heading{position:absolute;left:160px;top:30px}
.slider-arrows{position:absolute;left:1012px;top:36px;display:flex;gap:8px}
.client-name{position:absolute;left:163px;top:118px;font-family:"Open Sans",Arial,sans-serif;font-size:36px;color:#222;letter-spacing:-1px}
.testi-divider{position:absolute;left:423px;top:90px;width:1px;height:125px;background:var(--line)}
.quote{position:absolute;left:466px;top:92px;width:570px;font-style:italic;font-size:12px;line-height:22px;color:var(--muted)}
.quote .mark{color:var(--orange);font-weight:700;font-style:normal;font-size:15px}
.quote-author{position:absolute;left:466px;top:203px;font-size:12px;font-weight:700;color:var(--orange)}
.quote-author b{color:var(--navy)}

/* partner strip */
.partners{top:2158px;height:145px;background:var(--white)}
.partner{position:absolute;top:32px;width:212px;height:81px;border:1px solid var(--line);display:flex;align-items:center;justify-content:center;font-family:"Ubuntu",Arial,sans-serif;font-size:28px;color:#6c6c6c}

/* footer */
.site-footer{top:2303px;height:227px;background:var(--navy);border-top:4px solid var(--orange);color:var(--white)}
.footer-brand{position:absolute;left:162px;top:30px;display:flex;align-items:center;gap:8px;font-family:"Ubuntu",Arial,sans-serif;font-weight:500;font-size:30px}
.footer-brand .brand-square{background:var(--white)}
.footer-about{position:absolute;left:162px;top:104px;width:265px;font-size:11px;line-height:19px}
.footer-more{position:absolute;left:162px;top:190px;font-size:11px;color:var(--white);text-decoration:none}
.footer-map{left:442px;top:38px;width:341px;height:162px;background:linear-gradient(135deg,#e9e9e9,#d2d2d2)}
.footer-address{position:absolute;left:829px;top:40px;width:250px}
.footer-address h3{font-family:"Ubuntu",Arial,sans-serif;font-weight:400;font-size:15px;text-transform:uppercase}
.footer-address ul{list-style:none;margin-top:18px}
.footer-address li{font-size:11px;line-height:21px;display:flex;gap:8px;margin-bottom:2px}
.footer-address li svg{flex:none;margin-top:5px}
.copyright{top:2530px;height:71px;background:var(--navy-dark);color:#c9d3df;font-size:11px;text-align:center;line-height:71px}
</style>
</head>
<body>

<header class="section site-header">
  <div class="brand"><span class="brand-square"></span>Kavreo</div>
  <nav class="main-nav">
    <a class="active" href="#">Home</a>
    <a href="#">About us</a>
    <a href="#">Portfolio</a>
    <a href="#">Contact us</a>
  </nav>
  <div class="header-phone">
    <svg width="34" height="34" viewBox="0 0 34 34"><circle cx="17" cy="17" r="15" fill="none" stroke="#e8781f" stroke-width="2"/><path d="M12 10l3 0 1.5 4-2 1.5a9 9 0 0 0 4 4l1.5-2 4 1.5v3c0 1-1 2-2 2A13 13 0 0 1 10 12c0-1 1-2 2-2z" fill="#e8781f"/></svg>
    <div><span class="label">Call now for more information</span><span class="number">1300 648 907</span></div>
  </div>
</header>

<section class="section hero">
  <div class="placeholder hero-media" role="img" aria-label="Photo of a smiling woman using her smartphone"></div>
  <h1 class="hero-title"><span class="l1">Responsive Design to</span><span class="l2">Drive Mobile sales</span></h1>
  <div class="hero-dots"><span></span><span class="on"></span><span></span><span></span></div>
  <div class="hero-partners"><span>Torvista</span><span>QRX</span><span>DataVane</span><span>NCB</span></div>
</section>

<section class="section services">
  <div class="service" style="left:148px">
    <div class="service-icon orange"><svg width="34" height="26" viewBox="0 0 34 26"><rect x="6" y="3" width="22" height="15" rx="1" fill="none" stroke="#fff" stroke-width="2"/><path d="M2 21h30" stroke="#fff" stroke-width="2"/></svg></div>
    <div class="service-title">Torvista<br>System Audit</div>
    <p class="service-text">Sed ut perspiciatis unlorede nis natus error sit voluptatem accusaum doloremque laulorediantiumto.</p>
    <a class="service-link" href="#">CLICK HERE</a>
  </div>
  <div class="service" style="left:377px">
    <div class="service-icon"><svg width="30" height="30" viewBox="0 0 30 30"><path d="M27 3L3 13l8 3 2 9 4-6 6 4z" fill="#fff"/></svg></div>
    <div class="service-title">Torvista<br>Performance Optimisation</div>
    <p class="service-text">Sed ut perspiciatis unlorede nis natus error sit voluptatem accusaum doloremque laulorediantiumto.</p>
    <a class="service-link" href="#">CLICK HERE</a>
  </div>
  <div class="service" style="left:608px">
    <div class="service-icon"><svg width="30" height="30" viewBox="0 0 30 30"><circle cx="15" cy="15" r="12" fill="#fff"/><path d="M9 10c3 0 4 2 3 4s1 4 3 4M18 8c0 3 2 3 4 3M17 25c0-3 2-4 4-4" stroke="#0c3a6e" stroke-width="2" fill="none"/></svg></div>
    <div class="service-title">Torvista Website<br>Emergency Recovery</div>
    <p class="service-text">Sed ut perspiciatis unlorede nis natus error sit voluptatem accusaum doloremque laulorediantiumto.</p>
    <a class="service-link" href="#">CLICK HERE</a>
  </div>
  <div class="service" style="left:838px">
    <div class="service-icon"><svg width="34" height="30" viewBox="0 0 34 30"><circle cx="13" cy="17" r="8" fill="none" stroke="#fff" stroke-width="4" stroke-dasharray="4 2.3"/><circle cx="13" cy="17" r="3" fill="#fff"/><circle cx="25" cy="8" r="5" fill="none" stroke="#fff" stroke-width="3" stroke-dasharray="3 1.8"/></svg></div>
    <div class="service-title">Torvista Development<br>Infrastructure Hosting</div>
    <p class="service-text">Sed ut perspiciatis unlorede nis natus error sit voluptatem accusaum doloremque laulorediantiumto.</p>
    <a class="service-link" href="#">CLICK HERE</a>
  </div>
</section>

<section class="section why">
  <div class="why-body">
    <h2 class="heading"><span class="heading-mark"></span>Why Kavreo E- Commerce?</h2>
    <p class="copy">Fast Torvista-based online stores, built on time and to specification, backed by effective, focused support, means that our clients are among the happiest in the eCommerce world.</p>
    <p class="copy">Sed ut perspiciatis unde omnis iste natus error sit voluptatem accusantium doloremque laudantium, totam rem aperiam, eaque ipsa quae ab illo inventore veritatis et quasi archite cto beatae vitae dicta sunt explicabo.emo enim ipsam voluptatem quiaaspernatur aut odit aut fugit, sed quia consequunt.</p>
    <a class="btn" href="#">Contact us now!</a>
  </div>
  <div class="placeholder why-media" role="img" aria-label="Illustration of colourful shopping bags beside a computer mouse"></div>
</section>

<section class="section what">
  <h2 class="heading"><span class="heading-mark"></span>What We Do.</h2>
  <p class="what-text">From support, maintenance and upgrades to redesigns, migrations and full site builds, we make your online store do what you need it to do.Sed sit perspiciatis unde omnis iste natus error sit voluptatem accusantium doloremque laudantium, totam rem aperiam, eaque ipsa quae ab illo inventore veritatis et quasi archite cto beatae vitae dicta sunt explicabo.emoium doloremque laudantium, totam rem aperiam, eaque ipsa quae ab illo inventore veritatis et quasi archite cto beatae vitae dicta sunt explicabo.emo enim ipsam voluptatem quia. aspernatur aut odit.</p>
  <a class="btn-ghost" href="#">READ MORE</a>
</section>

<section class="section platform">
  <div class="placeholder platform-media" role="img" aria-label="Illustration of a shopping cart with parcels on a tablet"></div>
  <div class="platform-body">
    <h2 class="heading"><span class="heading-mark"></span>Why Torvista and Kavreo?</h2>
    <p class="copy">Torvista is the world's leading open source eCommerce platform. No other open-source or free system offers out-of-the-box functionality and search engine friendliness comparable to Torvista CE.</p>
    <p class="copy">Sed ut perspiciatis unde omnis iste natus error sit voluptatem accusantium doloremque laudantium, totam rem aperiam, eaque ipsa quae ab illo inventore veritatis et quasi archite cto beatae vitae dicta sunt explicabo.emo enim ipsam voluptatem quia.</p>
    <a class="btn" href="#">Read more about Torvista &amp; Kavreo</a>
  </div>
</section>

<section class="section testimonials">
  <h2 class="heading"><span class="heading-mark"></span>What Our Client Say About Us</h2>
  <div class="slider-arrows">
    <svg width="10" height="14" viewBox="0 0 10 14"><path d="M8 1L2 7l6 6" fill="none" stroke="#333b45" stroke-width="2"/></svg>
    <svg width="10" height="14" viewBox="0 0 10 14"><path d="M2 1l6 6-6 6" fill="none" stroke="#333b45" stroke-width="2"/></svg>
  </div>
  <div class="client-name">Lacewell</div>
  <div class="testi-divider"></div>
  <p class="quote"><span class="mark">&ldquo;</span> Sed ut perspiciatis unde omnis iste natus error sit voluptatem accusantium doloremque laudantium, totam rem aperiamaque ipsa quae ab illo inventore veritatis et quasi architecto beatae vitae dicta sunt explicabomo enim ipsam voluptatem quia voluptas sit aspernatur aut odit aut fugit, sed quia consege dicta sunt explicabomo enim ipsam voluptatem quia volu <span class="mark">&rdquo;</span></p>
  <div class="quote-author">JHON SMITH, <b>CITY NAME</b></div>
</section>

<section class="section partners">
  <div class="partner" style="left:162px">Torvista</div>
  <div class="partner" style="left:383px">QRX</div>
  <div class="partner" style="left:604px">DataVane</div>
  <div class="partner" style="left:824px">NCB</div>
</section>

<footer class="section site-footer">
  <div class="footer-brand"><span class="brand-square"></span>Kavreo</div>
  <p class="footer-about">Sed ut perspiciatis unde omnis iste natus error sit voluptatem accusantium doloremque laudantium, totam rem aperiam, eaque ipsa quae ab illo inven tore veritatis et quasi architecto beatae</p>
  <a class="footer-more" href="#">Read More</a>
  <div class="placeholder footer-map" role="img" aria-label="Street map showing the office location"></div>
  <div class="footer-address">
    <h3>Company Address</h3>
    <ul>
      <li><svg width="8" height="11" viewBox="0 0 8 11"><path d="M4 0a4 4 0 0 1 4 4c0 3-4 7-4 7S0 7 0 4a4 4 0 0 1 4-4z" fill="#e8781f"/><circle cx="4" cy="4" r="1.5" fill="#0c3a6e"/></svg><span>Suite 42, Level 3|8 Wattlebrook Lane|<br>Fernvale Heights VIC 3999</span></li>
      <li><svg width="9" height="9" viewBox="0 0 9 9"><path d="M1 0h2l1 2.5-1.3 1a5 5 0 0 0 2.8 2.8l1-1.3L9 6v2c0 .6-.4 1-1 1A8 8 0 0 1 0 1c0-.6.4-1 1-1z" fill="#e8781f"/></svg><span>Phone:&nbsp; (1300 648 907)</span></li>
      <li><svg width="10" height="8" viewBox="0 0 10 8"><rect width="10" height="8" rx="1" fill="#e8781f"/><path d="M0 1l5 3.5L10 1" stroke="#0c3a6e" fill="none"/></svg><span>Email: support@kavreo.example</span></li>
    </ul>
  </div>
</footer>

<div class="section copyright">&copy; 2016 All copyrights Reserved. Kavreo E-Commerce</div>

</body>
</html>
```